Bright Pelvicare Business Card

Need a business card for a surgical practice called Bright Pelvicare. We have recently selected a logo (attached). The business card will need to have two formats:
1) One with the logo/physician name/ contact info on the front and location information on the back.
2) One in "appointment reminder card" style with the logo/ contact info/ date/ time on the front and the location information on the back.

The front side should include the following information:
- Logo
- Rohan K. Desai, MD FACOG
- phone: 469-555-0182
- fax: 1-469-555-0317
- email: admin@brightpelvi.com
- website: www.brightpelvicare.com

The back side should have the office locations listed:
4518 Kestrel Ave, Plano, TX 75198
3920 Bramwell Rd, Plano, TX 75147
2245 Silverpine Ln, Irving, TX 75163
815 W Garnet Ave S310, Dallas, TX 75284
3614 Lantern Blvd, Grand Prairie, TX 75179
7405 Amberly Crest Dr, San Antonio, TX 78391
5812 Tolliver Rd, Pasadena, TX 77639

Target Market(s)

1. Other physicians who might refer patients
2. Female patients

Industry/Entity Type

Business

Font styles to use
Other font styles liked:
• Tahoma for lettering

Requirements
Must have
• As per the instructions
Should not have
• No other images needed -- please try to keep font consistent with logo design. Can use Tahoma as the font for lettering.

```html
<!DOCTYPE html>
<html lang="en">
<head>
<meta charset="utf-8">
<title>Bright Pelvicare – Business Card</title>
<link href="https://fonts.googleapis.com/css2?family=Michroma&family=PT+Sans:wght@400&display=swap" rel="stylesheet">
<style>
  :root {
    --page: #ffffff;
    --blue-bright: #1230f0;
    --blue-mid: #1020c8;
    --navy: #08086e;
    --glow: #ffffff;
    --glow-soft: #8f9cf0;
    --brand-blue: #2f5fb8;
    --accent-red: #e0282c;
    --info-yellow: #f2e430;
  }
  html, body {
    margin: 0;
    padding: 0;
    width: 1200px;
    height: 743px;
    overflow: hidden;
    background: var(--page);
  }
  .canvas {
    position: relative;
    width: 1200px;
    height: 743px;
  }
  .card {
    position: absolute;
    overflow: hidden;
    background:
      radial-gradient(circle at var(--gx) var(--gy), var(--glow) 0, rgba(255,255,255,0.85) 40px, rgba(143,156,240,0.7) 110px, rgba(60,80,230,0.25) 170px, rgba(16,32,200,0) 230px),
      linear-gradient(90deg, var(--blue-bright) 0%, var(--blue-mid) 45%, var(--navy) 100%);
  }
  .card--front { left: 47px; top: 138px; width: 523px; height: 326px; --gx: 200px; --gy: 155px; }
  .card--back  { left: 589px; top: 137px; width: 522px; height: 324px; --gx: 225px; --gy: 145px; }
  .card__decor {
    position: absolute;
    inset: 0;
    width: 100%;
    height: 100%;
  }
  .brand-name {
    position: absolute;
    margin: 0;
    font-family: "PT Sans", Tahoma, sans-serif;
    font-weight: 400;
    color: var(--brand-blue);
    white-space: nowrap;
  }
  .card--front .brand-name {
    left: 112px; top: 176px;
    font-size: 18px;
  }
  .brand-mark {
    position: absolute;
    border-radius: 50%;
    background: var(--accent-red);
  }
  .card--front .brand-mark { left: 206px; top: 140px; width: 26px; height: 26px; }
  .card--back .brand-name {
    left: 130px; top: 138px;
    font-size: 26px;
  }
  .card--back .brand-mark { left: 208px; top: 85px; width: 40px; height: 40px; }
  .contact {
    position: absolute;
    right: 12px;
    top: 227px;
    margin: 0;
    text-align: right;
    font-family: "Michroma", Tahoma, sans-serif;
    font-variant: small-caps;
    line-height: 16.3px;
  }
  .contact__name {
    display: block;
    color: var(--accent-red);
    font-size: 12px;
    letter-spacing: 0.5px;
  }
  .contact__line {
    display: block;
    color: var(--info-yellow);
    font-size: 10.5px;
    letter-spacing: 0.6px;
  }
  .locations {
    position: absolute;
    right: 18px;
    top: 205px;
    margin: 0;
    padding: 0;
    list-style: none;
    text-align: right;
    font-family: "Michroma", Tahoma, sans-serif;
    font-variant: small-caps;
    font-size: 8.4px;
    letter-spacing: 0.4px;
    line-height: 13.4px;
    color: var(--info-yellow);
  }
  .locations__gap { margin-top: 4px; }
</style>
</head>
<body>
<main class="canvas">
  <svg width="0" height="0" style="position:absolute" aria-hidden="true">
    <defs>
      <symbol id="sparkle" viewBox="-10 -10 20 20">
        <path d="M0,-10 L1.1,-1.1 L10,0 L1.1,1.1 L0,10 L-1.1,1.1 L-10,0 L-1.1,-1.1 Z" fill="#ffffff"/>
        <circle r="1.8" fill="#ffffff"/>
      </symbol>
      <linearGradient id="beam-fade" x1="0" y1="0" x2="1" y2="1">
        <stop offset="0" stop-color="#ffffff" stop-opacity="0.35"/>
        <stop offset="0.5" stop-color="#ffffff" stop-opacity="0.45"/>
        <stop offset="1" stop-color="#ffffff" stop-opacity="0.7"/>
      </linearGradient>
    </defs>
  </svg>

  <section class="card card--front" aria-label="Card front">
    <svg class="card__decor" viewBox="0 0 523 326" aria-hidden="true">
      <polygon points="60,0 0,85 0,100 503,324 460,318" fill="url(#beam-fade)"/>
      <use href="#sparkle" x="329" y="11" width="20" height="20"/>
      <use href="#sparkle" x="122" y="56" width="24" height="24"/>
      <use href="#sparkle" x="409" y="36" width="18" height="18"/>
      <use href="#sparkle" x="348" y="73" width="18" height="18"/>
      <use href="#sparkle" x="459" y="63" width="12" height="12"/>
      <use href="#sparkle" x="417" y="93" width="16" height="16"/>
      <use href="#sparkle" x="460" y="118" width="18" height="18"/>
      <use href="#sparkle" x="364" y="129" width="26" height="26"/>
      <use href="#sparkle" x="423" y="148" width="18" height="18"/>
      <use href="#sparkle" x="16" y="133" width="12" height="12"/>
      <use href="#sparkle" x="89" y="142" width="20" height="20"/>
      <use href="#sparkle" x="187" y="225" width="12" height="12"/>
      <use href="#sparkle" x="28" y="260" width="30" height="30"/>
      <use href="#sparkle" x="214" y="272" width="24" height="24"/>
    </svg>
    <span class="brand-mark" aria-hidden="true"></span>
    <p class="brand-name">Bright Pelvicare</p>
    <p class="contact">
      <span class="contact__name">Rohan K. Desai, MD FACOG</span>
      <span class="contact__line">phone: 469-555-0182</span>
      <span class="contact__line">fax:1-469-555-0317</span>
      <span class="contact__line">email: admin@brightpelvi.com</span>
      <span class="contact__line">website: www.brightpelvicare.com</span>
    </p>
  </section>

  <section class="card card--back" aria-label="Card back">
    <svg class="card__decor" viewBox="0 0 522 324" aria-hidden="true">
      <use href="#sparkle" x="329" y="9" width="20" height="20"/>
      <use href="#sparkle" x="407" y="34" width="20" height="20"/>
      <use href="#sparkle" x="118" y="51" width="26" height="26"/>
      <use href="#sparkle" x="347" y="70" width="20" height="20"/>
      <use href="#sparkle" x="414" y="90" width="18" height="18"/>
      <use href="#sparkle" x="360" y="126" width="26" height="26"/>
      <use href="#sparkle" x="423" y="147" width="18" height="18"/>
      <use href="#sparkle" x="86" y="139" width="20" height="20"/>
      <use href="#sparkle" x="16" y="131" width="12" height="12"/>
      <use href="#sparkle" x="185" y="224" width="12" height="12"/>
      <use href="#sparkle" x="28" y="260" width="30" height="30"/>
      <use href="#sparkle" x="175" y="268" width="26" height="26"/>
    </svg>
    <span class="brand-mark" aria-hidden="true"></span>
    <p class="brand-name">Bright Pelvicare</p>
    <ul class="locations">
      <li>4518 Kestrel Ave, Plano, TX 75198</li>
      <li>3920 Bramwell Rd, Plano, TX 75147</li>
      <li>2245 Silverpine Ln, Irving, TX 75163</li>
      <li>815 W Garnet Ave S310, Dallas, TX 75284</li>
      <li class="locations__gap">3614 Lantern Blvd, Grand Prairie, TX 75179</li>
      <li>7405 Amberly Crest Dr, San Antonio, TX 78391</li>
      <li>5812 Tolliver Rd, Pasadena, TX 77639</li>
    </ul>
  </section>
</main>
</body>
</html>
```